Sparrow Haulage needs a business card design.

Design a double-sided business card for new freight business. On the front, would like to see our logo along with the following info:

Martin Obuya
CEO/FOUNDER
555-206-7142
martinobuya@sparrow-haulage.example

On the reverse side, we would like to use the graphic image of our logo only without the Sparrow Haulage name.

```html
<!DOCTYPE html>
<html lang="en">
<head>
<meta charset="utf-8">
<title>Sparrow Haulage – Business Card</title>
<link rel="stylesheet" href="https://fonts.googleapis.com/css2?family=Michroma&family=Roboto:wght@400&display=swap">
<style>
  :root {
    --navy: #1b1a5c;
    --red: #b31c25;
    --white: #ffffff;
    --ink: #1a1a1a;
    --backdrop: #6b6b6b;
  }
  * { margin: 0; padding: 0; box-sizing: border-box; }
  html, body {
    width: 1200px; height: 1200px; overflow: hidden;
    background: var(--backdrop);
  }
  .card {
    position: absolute;
    left: 240px;
    width: 720px; height: 420px;
    box-shadow: 0 4px 14px rgba(0,0,0,0.35);
    overflow: hidden;
  }
  .card--front { top: 142px; background: var(--white); }
  .card--back  { top: 638px; background: var(--red); }

  .brand {
    position: absolute; left: 80px; top: 92px;
    display: flex; align-items: center; gap: 28px;
    font-family: "Michroma", sans-serif;
    line-height: 1.05;
    letter-spacing: 4px;
    color: var(--navy);
  }
  .brand__mark { width: 56px; height: 56px; flex: none; background: var(--red); }
  .brand__name {
    font-size: 27px;
    -webkit-text-stroke: 1px currentColor;
  }

  .back-mark {
    position: absolute;
    left: 328px; top: 178px;
    width: 64px; height: 64px;
    background: var(--white);
  }

  .holder {
    position: absolute; left: 164px; top: 240px;
  }
  .holder__name {
    font-family: "Michroma", sans-serif;
    font-weight: 400;
    font-size: 21px;
    letter-spacing: 1px;
    -webkit-text-stroke: 1.3px currentColor;
    line-height: 1.2;
  }
  .holder__first { color: var(--navy); margin-right: 14px; }
  .holder__last { color: var(--red); }
  .holder__title {
    font-family: "Roboto", sans-serif;
    font-size: 19px; letter-spacing: 1.4px;
    color: var(--ink); margin-top: 4px;
  }

  .contact {
    position: absolute; left: 164px; top: 316px;
    list-style: none;
    font-family: "Roboto", sans-serif;
    font-size: 19px; letter-spacing: 0.8px;
    color: var(--ink);
  }
  .contact__item { display: flex; align-items: center; height: 24px; }
  .contact__icon { width: 15px; height: 15px; margin-right: 13px; flex: none; }

  .band { position: absolute; bottom: 0; height: 12px; }
  .band--red { left: 0; width: 156px; background: var(--red); }
  .band--navy { left: 164px; right: 0; background: var(--navy); }
</style>
</head>
<body>
  <section class="card card--front" aria-label="Business card front">
    <div class="brand">
      <span class="brand__mark"></span>
      <span class="brand__name">SPARROW<br>HAULAGE</span>
    </div>

    <div class="holder">
      <h1 class="holder__name"><span class="holder__first">MARTIN</span><span class="holder__last">OBUYA</span></h1>
      <p class="holder__title">CEO/FOUNDER</p>
    </div>

    <ul class="contact">
      <li class="contact__item">
        <svg class="contact__icon" viewBox="0 0 16 16" aria-hidden="true">
          <path d="M3 1.5l2.5 0 1.2 3.2-1.6 1.2c.8 1.8 2.2 3.2 4 4l1.2-1.6 3.2 1.2v2.5c0 .8-.7 1.5-1.5 1.5C6.6 13.5 2.5 9.4 1.5 3 1.5 2.2 2.2 1.5 3 1.5z" fill="var(--red)"/>
        </svg>
        555-206-7142
      </li>
      <li class="contact__item">
        <svg class="contact__icon" viewBox="0 0 16 16" aria-hidden="true">
          <rect x="1.5" y="3.5" width="13" height="9.5" rx="1" fill="none" stroke="var(--red)" stroke-width="1.6"/>
          <path d="M2 4l6 5 6-5" fill="none" stroke="var(--red)" stroke-width="1.6"/>
        </svg>
        martinobuya@sparrow-haulage.example
      </li>
      <li class="contact__item">
        <svg class="contact__icon" viewBox="0 0 16 16" aria-hidden="true">
          <circle cx="8" cy="8" r="7" fill="var(--red)"/>
          <path d="M5 4c1 1 2 1 2 2.5S5 8 5 9.5 6.5 12 7 14M10 3c-1 1.5 0 2.5 1.5 3S13 8 12 9.5" fill="none" stroke="var(--white)" stroke-width="1.2"/>
        </svg>
        www.sparrow-haulage.example
      </li>
    </ul>

    <div class="band band--red"></div>
    <div class="band band--navy"></div>
  </section>

  <section class="card card--back" aria-label="Business card back">
    <span class="back-mark" role="img" aria-label="Brand mark"></span>
  </section>
</body>
</html>
```